Quarveth Capital LLC

Need Professional Business cards for New Investment Fund

Target Market(s)

High Quality investors

Industry/Entity Type

Financial

Contact Information for Business Card

Phone Number +1 555 284 6190
Name Lukas Varenko
Title Fund Manager
email lv@FundQuarveth.com
Website www.FundQuarveth.com

Colors

Designer to choose colors to be used in the design.

Requirements
Must have
• Must have our Logo and all of the above. Must be made so lettering and loge can be raised

```html
<!DOCTYPE html>
<html lang="en">
<head>
<meta charset="utf-8">
<title>Quarveth Capital LLC — Business Card</title>
<link href="https://fonts.googleapis.com/css2?family=Jost:wght@400;500;600&family=Raleway:wght@400;500&display=swap" rel="stylesheet">
<style>
  :root {
    --backdrop: #1f1f1f;
    --fund-green: #5aba47;
    --fund-green-bright: #4fc23a;
    --slate: #434d42;
    --slate-deep: #3a4239;
    --paper-white: #ffffff;
  }
  html, body {
    margin: 0;
    padding: 0;
    width: 1200px;
    height: 900px;
    overflow: hidden;
    background: var(--backdrop);
  }
  .canvas {
    position: relative;
    width: 1200px;
    height: 900px;
  }
  .card {
    position: absolute;
    left: 250px;
    width: 700px;
    height: 400px;
    overflow: hidden;
  }
  /* Front side */
  .card-front {
    top: 35px;
    background: var(--fund-green);
  }
  .front-wordmark {
    position: absolute;
    left: 0;
    right: 0;
    top: 165px;
    display: flex;
    justify-content: center;
    align-items: center;
    gap: 14px;
    font-family: "Jost", sans-serif;
    font-weight: 500;
    font-size: 50px;
    line-height: 1;
    letter-spacing: 5px;
    color: var(--paper-white);
  }
  .front-wordmark .mark-square {
    width: 24px;
    height: 24px;
    background: var(--paper-white);
  }
  .front-base-band {
    position: absolute;
    bottom: 0;
    left: 240px;
    width: 225px;
    height: 12px;
    background: var(--slate-deep);
  }
  /* Back side */
  .card-back {
    top: 465px;
    background: var(--slate);
  }
  .back-wordmark {
    position: absolute;
    left: 70px;
    top: 60px;
    display: flex;
    align-items: center;
    gap: 10px;
    font-family: "Jost", sans-serif;
    font-weight: 500;
    font-size: 32px;
    line-height: 1;
    letter-spacing: 4px;
    color: var(--fund-green-bright);
  }
  .back-wordmark .mark-square {
    width: 18px;
    height: 18px;
    background: var(--fund-green-bright);
  }
  .divider {
    position: absolute;
    left: 70px;
    right: 60px;
    top: 218px;
    height: 2px;
    background: var(--fund-green-bright);
  }
  .holder {
    position: absolute;
    left: 70px;
    top: 242px;
  }
  .holder-name {
    margin: 0;
    font-family: "Jost", sans-serif;
    font-weight: 600;
    font-size: 26px;
    line-height: 1.2;
    letter-spacing: 1px;
    text-transform: uppercase;
    color: var(--paper-white);
  }
  .holder-title {
    margin: 2px 0 0;
    font-family: "Raleway", sans-serif;
    font-weight: 400;
    font-size: 18px;
    color: var(--paper-white);
  }
  .contacts {
    position: absolute;
    right: 60px;
    top: 272px;
    margin: 0;
    padding: 0;
    list-style: none;
    font-family: "Raleway", sans-serif;
    font-size: 19px;
    color: var(--paper-white);
  }
  .contacts li {
    display: flex;
    justify-content: flex-end;
    align-items: center;
    gap: 12px;
    height: 30px;
  }
  .contacts svg {
    width: 16px;
    height: 16px;
    flex: none;
  }
  .back-base-band {
    position: absolute;
    bottom: 0;
    left: 50px;
    width: 220px;
    height: 6px;
    background: var(--fund-green-bright);
  }
</style>
</head>
<body>
<main class="canvas">

  <section class="card card-front" aria-label="Card front">
    <div class="front-wordmark">
      <span class="mark-square"></span>
      <span class="wordmark-text">QUARVETH</span>
    </div>
    <div class="front-base-band"></div>
  </section>

  <section class="card card-back" aria-label="Card back">
    <div class="back-wordmark">
      <span class="mark-square"></span>
      <span class="wordmark-text">QUARVETH</span>
    </div>

    <div class="divider"></div>

    <div class="holder">
      <h1 class="holder-name">Lukas Varenko</h1>
      <p class="holder-title">Title Fund Manager</p>
    </div>

    <ul class="contacts">
      <li>
        <span>+1 555 284 6190</span>
        <svg viewBox="0 0 16 16" aria-hidden="true">
          <path d="M3.5 1.5l2.5 0.5 1 3-1.6 1.2c0.8 1.7 2 2.9 3.6 3.6l1.2-1.6 3 1 0.5 2.5c-0.3 1-1.3 1.8-2.3 1.7C6 13.9 2.1 10 1.6 4.1 1.5 3 2.3 1.9 3.5 1.5z" fill="none" stroke="#4fc23a" stroke-width="1.5" stroke-linejoin="round"/>
        </svg>
      </li>
      <li>
        <span>lv@FundQuarveth.com</span>
        <svg viewBox="0 0 16 16" aria-hidden="true">
          <rect x="1.5" y="3.5" width="13" height="9" fill="none" stroke="#4fc23a" stroke-width="1.5"/>
          <path d="M1.5 3.5l6.5 5 6.5-5" fill="none" stroke="#4fc23a" stroke-width="1.5"/>
        </svg>
      </li>
      <li>
        <span>www.FundQuarveth.com</span>
        <svg viewBox="0 0 16 16" aria-hidden="true">
          <circle cx="8" cy="8" r="6.5" fill="none" stroke="#4fc23a" stroke-width="1.4"/>
          <ellipse cx="8" cy="8" rx="3" ry="6.5" fill="none" stroke="#4fc23a" stroke-width="1.2"/>
          <path d="M1.5 8h13M2.5 5h11M2.5 11h11" stroke="#4fc23a" stroke-width="1.1"/>
        </svg>
      </li>
    </ul>

    <div class="back-base-band"></div>
  </section>

</main>
</body>
</html>
```